Brightwave Reach - Business Card

We need a business card for a Social Media Marketing company that specializes in online marketing for small businesses in Canada using common Social Media platforms such as Pixlora, Chatterly, Blinkpost & Quibber.

I have uploaded a copy of our logo which I would like utilized in the business card. We would like the business card to be modern yet classy design.

Our website is www.brightwavereach.ca

Industry/Entity Type

Marketing

Contact Information for Business Card

Email: info@brightwavereach.ca
Website: www.brightwavereach.ca
Telephone: 604-555-0193

Colors

Designer to choose colors to be used in the design.

Requirements
Must have
• Social Media icons on reverse
• Please add some designs with color.

```html
<!DOCTYPE html>
<html lang="en">
<head>
<meta charset="utf-8">
<title>Brightwave Reach – Business Card</title>
<link href="https://fonts.googleapis.com/css2?family=Arimo:wght@400;700&display=swap" rel="stylesheet">
<style>
  :root {
    --backdrop: #4d4d4d;
    --card-light-top: #ffffff;
    --card-light-bottom: #d2d2d2;
    --card-dark: #3a3d40;
    --ink-dark: #333436;
    --ink-light: #e6e6e6;
    --chip: #d9d9d9;
  }
  * { margin: 0; padding: 0; box-sizing: border-box; }
  html, body { width: 1200px; height: 965px; overflow: hidden; }
  body {
    background: var(--backdrop);
    font-family: "Arimo", Arial, sans-serif;
    position: relative;
  }
  .card {
    position: absolute;
    left: 277px;
    width: 648px;
    height: 368px;
    box-shadow: 0 4px 14px rgba(0,0,0,.45);
  }
  .card--front {
    top: 97px;
    background: linear-gradient(180deg, var(--card-light-top) 0%, #f2f2f2 40%, var(--card-light-bottom) 100%);
    color: var(--ink-dark);
  }
  .card--back {
    top: 502px;
    background: var(--card-dark);
    color: var(--ink-light);
  }
  .brand-name {
    font-weight: 700;
    text-transform: uppercase;
    line-height: 1.05;
    text-align: center;
    letter-spacing: .5px;
  }
  .card--front .brand-name {
    position: absolute;
    left: 43px;
    top: 70px;
    width: 180px;
    font-size: 26px;
    color: var(--ink-dark);
  }
  .card--back .brand-name {
    position: absolute;
    left: 0;
    right: 0;
    top: 158px;
    font-size: 28px;
    color: var(--ink-light);
  }
  .person {
    position: absolute;
    left: 433px;
    top: 213px;
  }
  .person__name {
    font-size: 19px;
    font-weight: 400;
    letter-spacing: .5px;
    text-transform: uppercase;
  }
  .person__title {
    font-size: 14px;
    margin-top: 4px;
    padding-left: 3px;
  }
  .contacts {
    position: absolute;
    left: 433px;
    top: 281px;
    list-style: none;
    font-size: 14px;
  }
  .contacts li {
    display: flex;
    align-items: center;
    height: 19.5px;
  }
  .contacts svg {
    width: 12px;
    height: 12px;
    margin-right: 7px;
    flex: none;
  }
  .socials {
    position: absolute;
    top: 320px;
    left: 0;
    right: 0;
    display: flex;
    justify-content: center;
    gap: 11px;
    list-style: none;
  }
  .socials li {
    width: 31px;
    height: 31px;
    background: var(--chip);
  }
</style>
</head>
<body>
  <section class="card card--front" aria-label="Card front">
    <div class="brand-name">Brightwave<br>Reach</div>
    <div class="person">
      <div class="person__name">Daniel Hart</div>
      <div class="person__title">Managing Director</div>
    </div>
    <ul class="contacts">
      <li>
        <svg viewBox="0 0 12 12" aria-hidden="true"><path d="M2.5 1 L4.5 1 L5 3.5 L3.8 4.5 C4.5 6 5.8 7.4 7.5 8.2 L8.5 7 L11 7.5 L11 9.5 C11 10.3 10.3 11 9.5 11 C5 11 1 7 1 2.5 C1 1.7 1.7 1 2.5 1 Z" fill="none" stroke="#333436" stroke-width="1.1"/></svg>
        604-555-0193
      </li>
      <li>
        <svg viewBox="0 0 12 12" aria-hidden="true"><rect x="1" y="2.5" width="10" height="7" fill="none" stroke="#333436" stroke-width="1.1"/><path d="M1 2.5 L6 6.5 L11 2.5" fill="none" stroke="#333436" stroke-width="1.1"/></svg>
        info@brightwavereach.ca
      </li>
      <li>
        <svg viewBox="0 0 12 12" aria-hidden="true"><circle cx="6" cy="6" r="5" fill="none" stroke="#333436" stroke-width="1.1"/><ellipse cx="6" cy="6" rx="2.2" ry="5" fill="none" stroke="#333436" stroke-width="1"/><path d="M1 6 H11 M2 3.5 H10 M2 8.5 H10" stroke="#333436" stroke-width="0.9"/></svg>
        www.brightwavereach.ca
      </li>
    </ul>
  </section>

  <section class="card card--back" aria-label="Card back">
    <div class="brand-name">Brightwave<br>Reach</div>
    <ul class="socials">
      <li role="img" aria-label="Chatterly"></li>
      <li role="img" aria-label="Quibber"></li>
      <li role="img" aria-label="Pixlora"></li>
      <li role="img" aria-label="Linkora"></li>
    </ul>
  </section>
</body>
</html>
```